Ductless Mini Split Business Website

Copper Fern Services is looking to design an eye catching educational website about installing Ductless mini splits.

Similar to this company.
https://www.halvikstream.com/

Coding

Coded - Design and coding required

```html
<!DOCTYPE html>
<html lang="en">
<head>
<meta charset="utf-8">
<title>Copper Fern Services – Ductless Mini-Splits</title>
<link href="https://fonts.googleapis.com/css2?family=BenchNine:wght@300;400&family=Lato:ital,wght@0,400;0,700;1,400&family=Oswald:wght@400;500&family=Teko:wght@300;400&family=Varela+Round&display=swap" rel="stylesheet">
<style>
:root{
  --olive:#4e561c;
  --yellow:#f7d417;
  --gold:#f4c21c;
  --green:#8cc63f;
  --green-dark:#78ad34;
  --green-btn:#5cbf6b;
  --blue:#1d5fc9;
  --navy:#14307f;
  --brown:#a87100;
  --purple:#5a2d8c;
  --red:#c8102e;
  --text:#666;
  --dark:#333;
  --list:#3d6a8e;
  --sky:#cfe8f7;
}
*{margin:0;padding:0;box-sizing:border-box}
html,body{width:1200px;height:4263px;overflow:hidden}
body{position:relative;font-family:"Lato",sans-serif;color:var(--text);background:#fff}
.abs{position:absolute}
.ph{position:absolute}

/* header */
.topbar{left:0;top:0;width:1200px;height:41px;background:var(--olive)}
.topbar .tag{left:71px;top:14px;font-size:10px;color:#d8d07a;letter-spacing:.2px}
.btn-quote,.btn-call{top:8px;height:27px;border-radius:4px;color:#fff;font:700 11px "Lato",sans-serif;display:flex;align-items:center;justify-content:center}
.btn-quote{left:751px;width:139px;background:var(--green)}
.btn-call{left:902px;width:151px;background:#1e88e5;font-size:13px}
.navband{left:0;top:41px;width:1200px;height:67px;background:var(--yellow)}
.nav a{position:absolute;top:25px;font:500 14px "Oswald",sans-serif;color:#2b2b2b;text-decoration:none;text-transform:uppercase}
.logo-box{left:66px;top:46px;width:249px;height:100px;background:#fff;border-radius:6px;box-shadow:0 2px 6px rgba(0,0,0,.25);display:flex;flex-direction:column;align-items:center;justify-content:center;gap:6px;z-index:3}
.logo-name{display:flex;align-items:center;gap:8px;font:700 20px "Lato",sans-serif;color:#2b2b2b}
.logo-dot{width:16px;height:16px;border-radius:50%;background:var(--gold)}
.logo-sub{font:700 19px "Lato",sans-serif;color:#111}

/* hero */
.hero{left:0;top:108px;width:1200px;height:442px;background:linear-gradient(90deg,#5b6b55 0%,#8c8f86 30%,#b9b7b0 60%,#9e9c97 100%)}
.hero-title{left:0;top:262px;width:1200px;text-align:center;font:400 57px/55px "Oswald",sans-serif;color:var(--gold);letter-spacing:1px;text-transform:uppercase;text-shadow:0 0 3px #5a4a00}

/* tiles */
.tile{width:311px;height:232px;background:var(--green);color:#fff;text-align:center;display:flex;flex-direction:column;align-items:center;justify-content:center;padding:0 18px}
.tile svg{margin-bottom:8px}
.tile h3{font:400 23px/27px "Lato",sans-serif;text-transform:uppercase}
.tile p{font:italic 10px/16px "Lato",sans-serif;margin-top:6px}

/* banner */
.banner{left:0;top:1069px;width:1200px;height:487px;background:linear-gradient(180deg,#e3e3e3,#fafafa)}
.banner-h{left:570px;top:1152px;width:505px;text-align:center;font:400 44px "Varela Round",sans-serif;color:var(--blue)}
.banner-p{left:555px;top:1203px;width:535px;text-align:center;font:400 31px/38px "Varela Round",sans-serif;color:#2a63c3}
.btn-learn{left:736px;top:1304px;width:169px;height:45px;background:var(--navy);border-radius:6px;color:#fff;font:400 14px "Lato",sans-serif;letter-spacing:1px;display:flex;align-items:center;justify-content:center;box-shadow:0 3px 6px rgba(0,0,0,.3)}
.thumb{top:1415px;height:124px;border:4px solid #fff;box-shadow:0 2px 5px rgba(0,0,0,.2);background:linear-gradient(180deg,#c9b8a4,#8a7768)}

/* services band */
.svc-band{left:0;top:1561px;width:1200px;height:314px;background:var(--brown)}
.svc-h{left:58px;top:1590px;font:300 58px "Teko",sans-serif;color:var(--yellow);letter-spacing:2px}
.svc-p{left:58px;top:1670px;width:488px;font:400 20px/25px "BenchNine",sans-serif;color:#fff;text-align:justify}
.diagram{left:581px;top:1585px;width:561px;height:264px;background:#fff;border-radius:6px;padding:22px}
.diagram-fill{width:100%;height:100%;border-radius:4px;background:linear-gradient(90deg,#e7ecf6 0%,#f6f7fb 45%,#f6eaec 100%)}

/* products */
.col-h{font:400 24px/26px "Lato",sans-serif;color:var(--green-dark);text-align:center;text-transform:uppercase;width:311px}
.col-p{font:400 14px/28px "Lato",sans-serif;color:#777;width:315px;text-align:justify}
.col-list{list-style:none;font:italic 14px/28px "Lato",sans-serif;color:var(--list)}
.col-list li::before{content:"";display:inline-block;width:5px;height:5px;border-radius:50%;background:var(--green);margin:0 10px 2px 4px}
.prod{background:linear-gradient(90deg,#c9cdd1,#f1f2f3 50%,#b7bbbf)}

/* why choose */
.why{left:0;top:2800px;width:1200px;height:639px;background:var(--purple)}
.why-h{left:93px;top:2880px;font:400 56px/62px "Teko",sans-serif;color:var(--green);letter-spacing:2px;text-transform:uppercase}
.why-item{left:94px;width:420px;color:#fff}
.why-item h4{margin-left:63px;font:400 20px/26px "Lato",sans-serif}
.why-item p{margin-left:63px;font:400 13px/25px "Lato",sans-serif;margin-top:6px}
.why-item svg{position:absolute;left:0;top:0}
.form{left:538px;top:2888px;width:576px;height:463px;background:#fff}
.form-title{left:573px;top:2915px;font:400 17px "Lato",sans-serif;color:var(--green-dark)}
.lbl{left:573px;font:400 10px "Lato",sans-serif;color:#666}
.lbl b{color:var(--red);font-weight:400}
.inp{left:573px;width:354px;height:14px;background:#eee;font:400 10px "Lato",sans-serif;color:#aaa;padding-left:16px;line-height:14px}
.btn-est{left:573px;top:3270px;width:134px;height:45px;background:var(--green-btn);color:#fff;font:700 12px/13px "Lato",sans-serif;text-align:center;display:flex;align-items:center;justify-content:center}

/* testimonials */
.sky{left:0;top:3439px;width:1200px;height:450px;background:linear-gradient(180deg,#b6dcf3 0%,#e2f1fa 45%,#c3e2f5 100%)}
.card{background:#fff;box-shadow:0 1px 4px rgba(0,0,0,.1)}
.card-kicker{font:700 9px "Lato",sans-serif;color:#999;letter-spacing:2px;text-transform:uppercase;text-align:center}
.card-h1{font:700 24px "Varela Round",sans-serif;color:#5b3a8c;text-align:center}
.card-h2{font:700 25px "Varela Round",sans-serif;color:var(--red);text-align:center}
.card-small{font:400 8px/13px "Lato",sans-serif;color:#888;text-align:center}
.quote{font:italic 9px/15px "Lato",sans-serif;color:#8a6da0;text-align:center}
.arrow{top:3590px;font:400 30px "Lato",sans-serif;color:#556}
.brand{top:3748px;font:700 42px "Lato",sans-serif;letter-spacing:-1px;white-space:nowrap}

/* footer */
.footer{left:0;top:3889px;width:1200px;height:374px;background:linear-gradient(90deg,#10228a 0%,#1b2c95 55%,#c30d1a 100%)}
.foot-logo{left:154px;top:3922px;width:215px;height:111px;background:#fff;border-radius:6px;display:flex;flex-direction:column;align-items:center;justify-content:center;gap:8px}
.foot-logo .logo-name{font-size:16px}
.foot-logo .logo-sub{font-size:16px}
.foot-h{top:3955px;font:700 13px "Lato",sans-serif;color:#fff;letter-spacing:1px;text-transform:uppercase}
.news-img{left:400px;width:72px;height:66px;background:linear-gradient(180deg,#6e8597,#3e4a3a)}
.news-t{left:487px;width:105px;font:400 11px/15px "Lato",sans-serif;color:#fff}
.areas{left:639px;top:3985px;width:200px;font:400 12px/20px "Lato",sans-serif;color:#fff}
.social{top:3990px;width:30px;height:30px;background:#fff;border-radius:3px}
</style>
</head>
<body>

<!-- Header -->
<div class="abs topbar">
  <span class="abs tag">YOUR DUCTLESS MINI-SPLIT AND BOILER EXPERTS!</span>
  <span class="abs btn-quote">REQUEST A QUOTE</span>
  <span class="abs btn-call">CALL 555-014-2290</span>
</div>
<div class="abs navband">
  <nav class="nav">
    <a style="left:410px">Home</a>
    <a style="left:492px">About Us</a>
    <a style="left:591px">Ductless Heat Pumps</a>
    <a style="left:773px">FAQ</a>
    <a style="left:836px">Financing</a>
    <a style="left:955px">Reviews</a>
    <a style="left:1061px">Contact Us</a>
  </nav>
</div>
<div class="abs logo-box">
  <div class="logo-name"><span class="logo-dot"></span>Copper Fern Services</div>
  <div class="logo-sub">DUCTLESS EXPERTS</div>
</div>

<!-- Hero -->
<div class="ph hero" role="img" aria-label="Bright living room with large windows, stone wall, grey sofa and a wall-mounted mini-split unit"></div>
<h1 class="abs hero-title">Ductless Mini Splits Installation<br>Services Since 1999</h1>

<!-- Service tiles -->
<div class="abs tile" style="left:93px;top:574px">
  <svg width="60" height="44" viewBox="0 0 60 44" fill="none" stroke="#fff" stroke-width="2"><rect x="6" y="4" width="48" height="16" rx="3"/><line x1="12" y1="15" x2="48" y2="15"/><path d="M14 26v12M24 26v12M36 26v12M46 26v12"/></svg>
  <h3>Ductless A/C &amp; Heat Pump Installations</h3>
  <p>Need a ductless system installed?<br>We are your ductless mini-split experts!</p>
</div>
<div class="abs tile" style="left:424px;top:574px">
  <svg width="56" height="56" viewBox="0 0 56 56" fill="none" stroke="#fff" stroke-width="5" stroke-linecap="round"><line x1="10" y1="10" x2="46" y2="46"/><line x1="46" y1="10" x2="10" y2="46"/></svg>
  <h3>Start-up and Commissioning</h3>
  <p>Did you purchase a ductless system online?<br>Let us do the start up and commissioning!</p>
</div>
<div class="abs tile" style="left:753px;top:574px">
  <svg width="40" height="50" viewBox="0 0 40 50" fill="#fff"><rect x="10" y="14" width="22" height="32" rx="3"/><path d="M10 2c4 6 6 9 6 12a6 6 0 0 1-12 0c0-3 2-6 6-12z"/></svg>
  <h3>Boiler &amp; Combi Boiler Installations</h3>
  <p>Need a boiler system installed?<br>We are your boiler experts!</p>
</div>
<div class="abs tile" style="left:93px;top:819px">
  <svg width="60" height="36" viewBox="0 0 60 36" fill="none" stroke="#fff" stroke-width="2"><rect x="4" y="10" width="52" height="18" rx="3"/><line x1="10" y1="22" x2="50" y2="22"/><path d="M50 2v8M46 6h8" /></svg>
  <h3>Ductless System Cleanings</h3>
  <p>Professional cleaning services for your ductless system</p>
</div>
<div class="abs tile" style="left:424px;top:819px">
  <svg width="60" height="50" viewBox="0 0 60 50" fill="#fff"><rect x="6" y="4" width="36" height="11"/><rect x="6" y="19" width="36" height="11"/><rect x="6" y="34" width="36" height="11"/><path d="M52 10v14M45 17h14" stroke="#fff" stroke-width="2"/></svg>
  <h3>Server Room Cooling</h3>
  <p>Server room and data centre cooling with powerful ductless A/C systems</p>
</div>
<div class="abs tile" style="left:753px;top:819px">
  <svg width="50" height="48" viewBox="0 0 50 48" fill="#fff"><path d="M25 2l7 15 16 2-12 11 3 16-14-8-14 8 3-16L2 19l16-2z"/></svg>
  <h3>Interactive Remote</h3>
  <p>See what it feels like to be using the remote to control your ductless system. Your portable thermostat!</p>
</div>

<!-- Banner -->
<div class="abs banner"></div>
<div class="ph" style="left:40px;top:1092px;width:500px;height:364px;background:linear-gradient(90deg,#f4f4f4,#d9d6d2 55%,#e6e4e2)" role="img" aria-label="Wall-mounted mini-split unit and a woman holding a remote control"></div>
<h2 class="abs banner-h">Ductless Mini-Splits</h2>
<p class="abs banner-p">The most efficient air conditioning and heating for your home</p>
<span class="abs btn-learn">LEARN MORE ▸</span>
<div class="ph thumb" style="left:127px;width:214px;background:linear-gradient(180deg,#5b5e66,#9a8f86)" role="img" aria-label="Bedroom with wall unit"></div>
<div class="ph thumb" style="left:377px;width:214px" role="img" aria-label="Living room interior"></div>
<div class="ph thumb" style="left:626px;width:230px;background:linear-gradient(180deg,#a58d74,#6f5f54)" role="img" aria-label="Open kitchen interior"></div>
<div class="ph thumb" style="left:874px;width:230px" role="img" aria-label="Living room interior"></div>

<!-- Copper Fern services -->
<div class="abs svc-band"></div>
<h2 class="abs svc-h">COPPER FERN SERVICES</h2>
<p class="abs svc-p">We are also the experts when it comes to unparalleled ductless solutions. Whether you need repairs or maintenance for an existing unit or are considering switching your baseboard heating with a ductless heat pump, our trained technicians can do it all. With over 21 years of industry experience, we have proudly cared for the ductless needs of hundreds of residential properties throughout Oregon</p>
<div class="abs diagram">
  <div class="diagram-fill" role="img" aria-label="Diagram of single-zone and multi-zone ductless systems: outdoor units piped to one and to three indoor wall units"></div>
</div>

<!-- Products row 1 -->
<h3 class="abs col-h" style="left:116px;top:1918px">Ductless Mini-Splits</h3>
<p class="abs col-p" style="left:116px;top:1960px">High efficiency ductless air conditioners and heat pumps that can both cool and heat all year long. We have systems suitable for homes, offices, and server rooms.</p>
<ul class="abs col-list" style="left:116px;top:2101px">
  <li>Kestrel K-Series</li><li>R-Series &amp; Town-Multi®</li><li>Fenwave Halden®</li><li>Dovecrest</li><li>Pellucor</li><li>Larkspan</li>
</ul>
<div class="ph prod" style="left:343px;top:2099px;width:86px;height:172px" role="img" aria-label="Silver outdoor heat pump unit"></div>

<h3 class="abs col-h" style="left:447px;top:1918px">Hot Water Tanks</h3>
<p class="abs col-p" style="left:447px;top:1960px">Our best in class hot water tanks will suit any size home and provide hot water reliably and efficiently. Pair with a boiler to heat your home &amp; water simultaneously.</p>
<ul class="abs col-list" style="left:447px;top:2101px">
  <li>Bastrel Indirect Tanks</li><li>Trident Coil Smart®</li><li>Vendhaus Thermocell®</li>
</ul>
<div class="ph prod" style="left:675px;top:2099px;width:83px;height:172px;background:linear-gradient(90deg,#ddd,#fff 50%,#ccc)" role="img" aria-label="White indirect hot water tank"></div>

<h3 class="abs col-h" style="left:778px;top:1918px">Boilers &amp; Combi Boilers</h3>
<p class="abs col-p" style="left:778px;top:1986px">We sell, install and service a wide range of boilers including combination and wall-hung. We have the right boiler for your needs, be it a residential home or a large office complex.</p>
<ul class="abs col-list" style="left:778px;top:2127px">
  <li>Bastrel</li><li>Vendhaus</li><li>Lorne</li><li>NVR</li><li>Trident Coil</li>
</ul>
<div class="ph prod" style="left:1003px;top:2127px;width:86px;height:173px;background:linear-gradient(90deg,#cfd2d4,#f3f4f5 50%,#c8cbce)" role="img" aria-label="Wall-hung combi boiler"></div>

<!-- Products row 2 -->
<h3 class="abs col-h" style="left:116px;top:2320px">Tankless Water<br>Heaters</h3>
<p class="abs col-p" style="left:116px;top:2388px">We install the most efficient tankless water heaters in the Canadian market today! This results in dramatic reduction of carbon dioxide and increases the heater's efficiency level to over 93%! Some other brands may have a bit higher efficiency ratings, but there is a fine balance between the efficiency level and flow rate performance.</p>
<div class="ph prod" style="left:339px;top:2595px;width:88px;height:169px" role="img" aria-label="Tankless water heater"></div>

<h3 class="abs col-h" style="left:447px;top:2320px">Gas Fireplaces</h3>
<p class="abs col-p" style="left:447px;top:2360px">Vantor fireplaces are energy efficient, do not require power to heat your home and come in a wide variety of styles and options. So you can be sure that there is a Vantor Fireplace for you and let <i>halvikstream.com</i> help with your choice!</p>
<ul class="abs col-list" style="left:447px;top:2573px">
  <li>Vantor</li><li>Emberline® Log Sets</li>
</ul>
<div class="ph" style="left:670px;top:2540px;width:88px;height:174px;background:radial-gradient(circle at 55% 65%,#f08a1c 0,#a3380e 25%,#2a2a2a 55%,#555 100%)" role="img" aria-label="Gas fireplace with flames"></div>

<h3 class="abs col-h" style="left:778px;top:2320px">Solar Heating</h3>
<p class="abs col-p" style="left:778px;top:2360px">As the cleanest, most abundant and easily accessible form of energy on earth, start your sustainable energy approach with solar energy. A solar system not only showcases your commitment to the environment, it will increase your property value at the same time.</p>
<ul class="abs col-list" style="left:778px;top:2629px">
  <li>Vendhaus Sunmax®</li>
</ul>
<div class="ph prod" style="left:1003px;top:2598px;width:84px;height:174px;background:linear-gradient(90deg,#d8dadc,#fafafa 50%,#d0d2d4)" role="img" aria-label="Solar heating controller unit"></div>

<!-- Why choose -->
<div class="abs why"></div>
<h2 class="abs why-h">Why Choose<br>Copper Fern Services ?</h2>
<div class="abs why-item" style="top:3040px">
  <svg width="40" height="44" viewBox="0 0 40 44" fill="none" stroke="var(--green)" stroke-width="2"><rect x="6" y="4" width="24" height="34" rx="2"/><path d="M11 12h14M11 18h14M11 24h8"/><circle cx="28" cy="32" r="7"/></svg>
  <h4>0% Financing for 60 months</h4>
  <p>Providing options to our customers where it matters most. Offer applies to Tressa systems.</p>
</div>
<div class="abs why-item" style="top:3148px">
  <svg width="40" height="44" viewBox="0 0 40 44" fill="none" stroke="var(--green)" stroke-width="2"><path d="M4 18a16 14 0 0 1 32 0z"/><path d="M20 18v18a4 4 0 0 1-8 0"/></svg>
  <h4>365 Day, Money Back Guarantee</h4>
  <p>We have integrity, and stand behind our services to ensure that you are satisfied.</p>
</div>
<div class="abs why-item" style="top:3255px">
  <svg width="40" height="44" viewBox="0 0 40 44" fill="none" stroke="var(--green)" stroke-width="2"><circle cx="20" cy="14" r="9"/><path d="M6 40c0-9 6-14 14-14s14 5 14 14"/><path d="M10 10h20"/></svg>
  <h4>We Are the Experts in Ductless<br>Services</h4>
  <p>Not only can we perform the services with precision, but we can also educate you on why ductless is the way to do.</p>
</div>

<div class="abs form"></div>
<div class="abs form-title">BOOK AN APPOINTMENT HERE!</div>
<div class="abs lbl" style="top:2994px">Name <b>*</b></div>
<div class="abs inp" style="top:3020px"></div>
<div class="abs lbl" style="top:3047px">Email <b>*</b></div>
<div class="abs inp" style="top:3073px;width:362px">Your best email address</div>
<div class="abs lbl" style="top:3100px">Address <b>*</b></div>
<div class="abs inp" style="top:3126px"></div>
<div class="abs lbl" style="top:3153px">Please Describe Your Request <b>*</b></div>
<div class="abs inp" style="top:3174px;width:519px;height:85px;padding-top:8px">Message</div>
<div class="abs btn-est">Get Your Free<br>Estimate</div>

<!-- Testimonials -->
<div class="abs sky"></div>
<div class="abs card" style="left:86px;top:3464px;width:472px;height:199px"></div>
<div class="abs card-kicker" style="left:86px;top:3486px;width:472px">Air Conditioning &amp; Heating Services</div>
<div class="abs card-h1" style="left:86px;top:3510px;width:472px">Specializing In</div>
<div class="abs card-h2" style="left:86px;top:3540px;width:472px">Ductless Air Conditioning</div>
<p class="abs card-small" style="left:146px;top:3590px;width:352px">We specialize in designing and installing complete ductless comfort systems for both homes and businesses, as well as service and upkeep of those systems. Strong pride is taken in the craftsmanship of every install by our team. Give us a call for your air conditioning and heating needs.</p>
<div class="abs card" style="left:596px;top:3464px;width:488px;height:199px"></div>
<p class="abs quote" style="left:636px;top:3530px;width:408px">Marin and his team were very professional and patient to work with. Very helpful in helping us weigh several options and very fair with price. We bought a unit to support an old forced air system where heat and cooling could not reach the top floor. A single unit is now cooling the entire top floor and some of the main floor.</p>
<div class="abs" style="left:596px;top:3598px;width:488px;text-align:center;font:400 6px 'Lato',sans-serif;color:#8a6da0">Homeowner<br>Salem, OR</div>
<span class="abs arrow" style="left:54px">‹</span>
<span class="abs arrow" style="left:1096px">›</span>

<span class="abs brand" style="left:100px;color:#777">Larkspan</span>
<span class="abs brand" style="left:312px;color:#d8262e">Fenwave</span>
<div class="ph" style="left:505px;top:3715px;width:160px;height:160px;border-radius:50%;background:radial-gradient(circle,#e9f4fb 0%,#b9d6ec 60%,#cfe8f7 100%)" role="img" aria-label="Cartoon mascot character"></div>
<span class="abs brand" style="left:692px;font-size:30px;top:3758px;color:#1d5fc9">Pellucor</span>
<span class="abs brand" style="left:895px;color:#1d3f8a">Bastrel</span>

<!-- Footer -->
<div class="abs footer"></div>
<div class="abs foot-logo">
  <div class="logo-name"><span class="logo-dot"></span>Copper Fern Services</div>
  <div class="logo-sub">DUCTLESS EXPERTS</div>
</div>
<div class="abs foot-h" style="left:400px">Recent News</div>
<div class="ph news-img" style="top:3985px" role="img" aria-label="House exterior photo"></div>
<div class="abs news-t" style="top:3985px">Port Neches, TX Ductless Air Conditioner Installation</div>
<div class="ph news-img" style="top:4063px;background:linear-gradient(180deg,#3a2d1c,#a3701e)" role="img" aria-label="Myth-busting article graphic"></div>
<div class="abs news-t" style="top:4063px">BUSTING MYTHS ABOUT ELECTRIC &amp; DUCTLESS HEAT PUMPS</div>
<div class="ph news-img" style="top:4146px;background:linear-gradient(180deg,#8fa6b8,#5a6e55)" role="img" aria-label="Century-old house photo"></div>
<div class="abs news-t" style="top:4146px">Ductless Heating And Cooling In A Century-Old Nederland, TX Home</div>

<div class="abs foot-h" style="left:639px">Areas Served</div>
<div class="abs areas">We proudly offer our services to the following areas:<br><br>
• BEAUMONT, TX<br>• BRIDGE CITY, TX<br>• GROVES, TX<br>• NEDERLAND, TX<br>• ORANGE, TX<br>• PORT ARTHUR, TX<br>• PORT NECHES, TX</div>

<div class="abs foot-h" style="left:879px">Follow Us</div>
<div class="abs social" style="left:884px"></div>
<div class="abs social" style="left:926px"></div>
<div class="abs social" style="left:968px"></div>

</body>
</html>
```